Digital Billboard Design: Winter Sales Event

I own a boutique furniture store in Calgary, AB (larkhollowhome.ca) and I am looking to advertise our winter sale event on a new curved digital billboard (specs attached including required file type).

I have this billboard rented for 52-weeks so I will be looking to change the design every 4-weeks (i.e. this is intended to be an ongoing project).

The objective of this first billboard is to raise awareness around our annual winter sales event. The store itself is only a few blocks from the billboard so those commuting into downtown are just a short drive from the store.

I am looking for a fresh, clean, contemporary look that will grab your attention as you drive into downtown Calgary without presenting to much info so as to be distracting (and overwhelming -- the billboard does not need to contain all info on my current marketing material). I should also note that the store caters to a higher-end, more sophisticated clientele so the graphics need to reflect the brand (i.e. we are not Brenton Furniture or Couch Depot!).

I have attached three files:

Billboard specs
Current marketing material advertising sale (and all relevant data)
An idea that is from an American furniture store that I think is interesting

Target Market(s)

Upper middle class, sophisticated client who appreciates the finer things in life.

Industry/Entity Type

Furniture Store

Font styles to use
Sans Serif

Requirements
Must have
• Company Logo
• Winter Sales Event - 20 to 60% off
• Address: 2417 14th Ave SW
Nice to have
• Image of furniture -- see our website www.larkhollowhome.ca -- any photo from this site can be used
Should not have
• Too much text or visual distration

```html
<!DOCTYPE html>
<html lang="en">
<head>
<meta charset="utf-8">
<title>Winter Sales Event – Lark Hollow Home</title>
<link rel="stylesheet" href="https://fonts.googleapis.com/css2?family=Michroma&family=Montserrat:wght@500&display=swap">
<style>
  :root {
    --page: #ffffff;
    --edge-violet: #7a68b0;
    --mid-lilac: #c9c0e2;
    --glow: #ffffff;
    --flake: #a596cd;
    --headline: #ffffff;
    --headline-grey: #707070;
    --offer-grey: #7c7c7c;
    --offer-stroke: #5a5a5a;
    --brand: #4e4e50;
    --address: #5e5e60;
  }
  html, body {
    margin: 0;
    padding: 0;
    width: 1200px;
    height: 1000px;
    overflow: hidden;
    background: var(--page);
  }
  .canvas {
    position: relative;
    width: 1200px;
    height: 1000px;
    box-sizing: border-box;
    border: 1px solid #d8d4ec;
  }
  .billboard {
    position: absolute;
    left: 146px;
    top: 284px;
    width: 900px;
    height: 431px;
    background: linear-gradient(90deg,
      var(--edge-violet) 3%,
      var(--mid-lilac) 33%,
      var(--glow) 49%,
      var(--mid-lilac) 66%,
      var(--edge-violet) 97%);
    text-align: center;
  }
  .snowflake {
    position: absolute;
    left: 386px;
    top: 37px;
    width: 130px;
    height: 147px;
  }
  .headline {
    position: absolute;
    left: 0;
    right: 0;
    top: 207px;
    margin: 0;
    font-family: "Michroma", sans-serif;
    font-weight: 400;
    font-size: 38px;
    line-height: 1;
    color: var(--headline);
    letter-spacing: 0;
  }
  .headline .accent { color: var(--headline-grey); }
  .offer {
    position: absolute;
    left: 0;
    right: 0;
    top: 262px;
    margin: 0;
    font-family: "Michroma", sans-serif;
    font-size: 34px;
    line-height: 1;
    color: var(--offer-grey);
    -webkit-text-stroke: 1px var(--offer-stroke);
  }
  .brand {
    position: absolute;
    left: 0;
    right: 0;
    top: 327px;
    margin: 0;
    font-family: "Montserrat", sans-serif;
    font-weight: 500;
    font-size: 36px;
    line-height: 1;
    letter-spacing: 5px;
    color: var(--brand);
  }
  .address {
    position: absolute;
    left: 0;
    right: 0;
    top: 382px;
    margin: 0;
    font-family: "Michroma", sans-serif;
    font-size: 21px;
    line-height: 1;
    letter-spacing: 1.5px;
    color: var(--address);
  }
</style>
</head>
<body>
<main class="canvas">
  <section class="billboard" aria-label="Winter sales event billboard">
    <svg class="snowflake" viewBox="-65 -74 130 148" aria-hidden="true">
      <defs>
        <g id="flake-arm" stroke="var(--flake)" stroke-width="6" fill="none">
          <line x1="0" y1="0" x2="0" y2="-73"/>
          <polyline points="-23,-62 0,-48 23,-62"/>
        </g>
      </defs>
      <use href="#flake-arm"/>
      <use href="#flake-arm" transform="rotate(60)"/>
      <use href="#flake-arm" transform="rotate(120)"/>
      <use href="#flake-arm" transform="rotate(180)"/>
      <use href="#flake-arm" transform="rotate(240)"/>
      <use href="#flake-arm" transform="rotate(300)"/>
    </svg>

    <h1 class="headline">WINTER <span class="accent">SALES</span> EVENT</h1>
    <p class="offer">20 to 60% off</p>
    <p class="brand">LARK HOLLOW HOME</p>
    <p class="address">2417 14th Ave SW, CALGARY, AB.</p>
  </section>
</main>
</body>
</html>
```